Marlow Estate Fixers (Handyman / Home Improvement Company)

Looking for a double sided professional looking business card with Logo attached to be highlighted on one side and throwing in an image of a handyman as an option would be nice to see as well. We are a company focused on providing quality Handyman and Home improvement services in a timely manner that is done right the first time with integrity

Industry/Entity Type

Handyman / Home Improvement

Contact Information for Business Card

(LOGO, Name, Mobile and office phone numbers, email) on front side of card, (the words "The SOLUTION to all of your Handyman and Home Improvement needs" followed by "Family Owned and Operated" at the very bottom) on the back.

Colors
EB3D1F
EC4F4E
F09395
F8D3D4
FCEDEE

Requirements
Must have
• Red, Gray, Black Color scheme
Should not have
• No Yellow or Blue colors

```html
<!DOCTYPE html>
<html lang="en">
<head>
<meta charset="UTF-8">
<title>Marlow Estate Fixers – Business Card</title>
<link rel="stylesheet" href="https://fonts.googleapis.com/css2?family=Montserrat:wght@400;500;700;800&display=swap">
<style>
  :root {
    --bg: #3a3a3a;
    --card-dark: #2b2b2b;
    --card-dark-text: #1a1a1a;
    --card-dark-soft: #8a8a8a;
    --card-light: #ffffff;
    --ink: #111111;
    --ink-soft: #2a2a2a;
    --red: #eb3d1f;
  }
  * { box-sizing: border-box; margin: 0; padding: 0; }
  html, body { width: 1200px; height: 875px; overflow: hidden; }
  body {
    background: var(--bg);
    font-family: "Montserrat", sans-serif;
    position: relative;
  }
  .card {
    position: absolute;
    width: 560px;
    height: 320px;
    border-radius: 22px;
    box-shadow: 0 18px 40px rgba(0,0,0,.45);
  }
  .card-back {
    left: 80px; top: 110px;
    background: var(--card-dark);
    display: flex; flex-direction: column;
    align-items: center; justify-content: center;
    padding: 30px 40px;
    text-align: center;
  }
  .card-front {
    left: 560px; top: 445px;
    background: var(--card-light);
    display: flex; align-items: center;
    padding: 0 30px 0 36px;
  }
  .brand {
    display: flex; align-items: center; gap: 12px;
    font-weight: 800; text-transform: uppercase;
    letter-spacing: .02em; line-height: 1.05;
  }
  .brand-mark { width: 22px; height: 22px; flex: none; }
  .card-back .brand { color: var(--card-dark-text); font-size: 32px; }
  .card-back .brand-mark { background: var(--card-dark-text); width: 28px; height: 28px; }
  .tagline {
    margin-top: 28px;
    color: var(--card-dark-soft);
    font-size: 14px; font-weight: 500; line-height: 1.5;
    max-width: 400px;
  }
  .tagline strong { color: var(--red); font-weight: 700; }
  .family-note {
    position: absolute; bottom: 26px; left: 0; right: 0;
    color: var(--card-dark-soft);
    font-size: 11px; font-weight: 700;
    letter-spacing: .18em; text-transform: uppercase;
  }
  .card-front .brand { color: var(--red); font-size: 21px; width: 220px; }
  .card-front .brand-mark { background: var(--ink); }
  .divider {
    width: 2px; height: 190px; background: var(--red);
    margin: 0 20px 0 12px; flex: none;
  }
  .details { color: var(--ink-soft); font-size: 12.5px; line-height: 1.45; }
  .person-name { font-size: 22px; font-weight: 800; color: var(--ink); line-height: 1.1; }
  .person-name .surname { color: var(--red); }
  .person-role { font-size: 12.5px; font-weight: 500; margin-bottom: 12px; }
  .address { margin-bottom: 10px; }
  .contact-list { list-style: none; }
  .contact-list li { display: flex; align-items: center; gap: 8px; white-space: nowrap; }
  .contact-list svg { width: 12px; height: 12px; fill: var(--red); flex: none; }
  .contact-label { font-weight: 700; color: var(--ink); }
</style>
</head>
<body>
  <section class="card card-back" aria-label="Card back">
    <div class="brand"><span class="brand-mark"></span><span>Marlow Estate Fixers</span></div>
    <p class="tagline">The <strong>SOLUTION</strong> to all of your Handyman and Home Improvement needs</p>
    <p class="family-note">Family Owned and Operated</p>
  </section>

  <section class="card card-front" aria-label="Card front">
    <div class="brand"><span class="brand-mark"></span><span>Marlow Estate Fixers</span></div>
    <div class="divider"></div>
    <div class="details">
      <p class="person-name">Evan <span class="surname">Hollis</span></p>
      <p class="person-role">Managing Director</p>
      <p class="address">48 Harbor Lane,<br>Fairview, USA</p>
      <ul class="contact-list">
        <li>
          <svg viewBox="0 0 24 24"><path d="M6.6 10.8a15 15 0 0 0 6.6 6.6l2.2-2.2a1 1 0 0 1 1-.25 11.4 11.4 0 0 0 3.6.57 1 1 0 0 1 1 1V20a1 1 0 0 1-1 1A17 17 0 0 1 3 4a1 1 0 0 1 1-1h3.5a1 1 0 0 1 1 1c0 1.25.2 2.45.57 3.57a1 1 0 0 1-.25 1z"/></svg>
          <span><span class="contact-label">M</span> (08) 4410 2283</span>
        </li>
        <li>
          <svg viewBox="0 0 24 24"><path d="M6.6 10.8a15 15 0 0 0 6.6 6.6l2.2-2.2a1 1 0 0 1 1-.25 11.4 11.4 0 0 0 3.6.57 1 1 0 0 1 1 1V20a1 1 0 0 1-1 1A17 17 0 0 1 3 4a1 1 0 0 1 1-1h3.5a1 1 0 0 1 1 1c0 1.25.2 2.45.57 3.57a1 1 0 0 1-.25 1z"/></svg>
          <span><span class="contact-label">O</span> (08) 4410 2290</span>
        </li>
        <li>
          <svg viewBox="0 0 24 24"><path d="M2 5h20v14H2z M2 5l10 8 10-8" /></svg>
          hello@marlowfixers.com
        </li>
        <li>
          <svg viewBox="0 0 24 24"><circle cx="12" cy="12" r="10"/></svg>
          www.marlowfixers.com
        </li>
      </ul>
    </div>
  </section>
</body>
</html>
```